Banner Ad Designs for tick and flea products

We sell tick and flea products online and want some great banner designs for our online website to promote our tick and flea products.

The ads must be made up in both Flash and HTML5
Ads can be formatted as .JPEG or .GIF files.

Please see the following url for creative requirements
http://help.bannerkite.com/creative-requirements/

Creative licence no limits to your imagination!

Ads must be created in the following sizes:

- Banner – 468×60
- Square – 250×250
- Small Square – 200×200
- Leaderboard – 728×90
- Medium Rectangle – 300×250
- Chatterly – 100×72

please view our website at www.globalpawstore.com.au or .com to get a feel for our website.

The aim is to attract customers who want to save on tick and flea purchases for their pets (dogs and cats)

Target Market(s)

Anyone who owns a dog or cat

Industry/Entity Type

Online

Font styles to use
Sans Serif
Other font styles liked:
• creative licence on font styles

Requirements
Must have
• Must have a strong urge to entice customers to click through.

Images wording and text etc use creative lic
Nice to have
• Strong appeal to dog and cat owners and how they can save on flea and tick essentials.
Keep it simple but effective.
Be fun and playful and inviting.
Should not have
• Please do not use words like cheap - cheapest

Strobing & Flashing - Strobing, flashing backgrounds, or otherwise distracting ads are not allowed. Do not attempt to overtly distract the user from page content.

```html
<!DOCTYPE html>
<html lang="en">
<head>
<meta charset="utf-8">
<title>Tick and Flea Banner Set</title>
<link rel="stylesheet" href="https://fonts.googleapis.com/css2?family=Ubuntu:wght@400;500&family=PT+Sans:wght@400;700&display=swap">
<style>
  :root {
    --page: #ffffff;
    --leaf: #7ea832;
    --leaf-deep: #6e9628;
    --frame-line: #2f3d17;
    --sky-top: #bfe2f3;
    --sky-bottom: #2c92c9;
    --navy: #16188a;
    --lime: #2bd12b;
    --white: #ffffff;
    --button-top: #bfe4f6;
    --button-bottom: #4ba3d4;
    --caption: #444444;
    --photo-warm: #b89a7a;
    --photo-dark: #5a4636;
    --photo-pug: #c9a477;
  }
  * { margin: 0; padding: 0; box-sizing: border-box; }
  html, body { width: 1200px; height: 900px; overflow: hidden; background: var(--page); }
  .canvas { position: relative; width: 1200px; height: 900px; background: var(--page); }

  .banner {
    position: absolute; left: 63px; width: 1089px; height: 135px;
    background: var(--leaf); overflow: hidden;
  }
  .banner--save { top: 75px; }
  .banner--brand { top: 232px; }
  .banner--order { top: 387px; }
  .banner--sky {
    top: 543px; height: 132px;
    background: linear-gradient(to bottom, var(--sky-top) 0%, #7cc2e6 45%, var(--sky-bottom) 100%);
  }
  .banner__frame {
    position: absolute; left: 6px; top: 6px; right: 6px; bottom: 6px;
    border: 1px solid var(--frame-line);
  }
  .banner--sky .banner__frame { border-color: #1d5d84; }

  .photo { position: absolute; top: 0; height: 100%; }
  .photo--pets {
    left: 0; width: 170px;
    background:
      radial-gradient(ellipse at 45% 70%, var(--photo-warm) 0%, var(--photo-dark) 40%, rgba(255,255,255,0.9) 70%),
      linear-gradient(to right, #ffffff 0%, #ffffff 70%, rgba(255,255,255,0) 100%);
    -webkit-mask-image: linear-gradient(to right, #000 75%, transparent 100%);
    mask-image: linear-gradient(to right, #000 75%, transparent 100%);
  }
  .photo--pugs {
    right: 0; width: 165px;
    background: radial-gradient(ellipse at 55% 60%, var(--photo-pug) 0%, #8a6a48 40%, #f2efe8 72%);
    -webkit-mask-image: linear-gradient(to left, #000 78%, transparent 100%);
    mask-image: linear-gradient(to left, #000 78%, transparent 100%);
  }
  .photo--terrier {
    left: 20px; width: 140px;
    background: radial-gradient(ellipse at 50% 55%, #d8b27e 0%, #8c6a44 38%, rgba(255,255,255,0) 70%);
  }

  .headline {
    position: absolute; font-family: "Ubuntu", "PT Sans", sans-serif;
    color: var(--white); font-weight: 400; white-space: nowrap;
  }
  .headline--save {
    left: 170px; right: 165px; top: 10px; text-align: center;
    font-size: 43px; line-height: 54px;
  }
  .headline--protect {
    left: 170px; top: 44px; font-size: 36px; line-height: 44px;
    font-family: "PT Sans", sans-serif;
  }
  .headline--navy {
    left: 189px; top: 24px; color: var(--navy);
    font-family: "PT Sans", sans-serif; font-size: 37px; line-height: 44px;
  }
  .site-url {
    position: absolute; right: 257px; top: 78px;
    font-family: "PT Sans", sans-serif; font-size: 22px; color: var(--lime);
  }

  .brand-box {
    position: absolute; right: 8px; top: 8px; width: 229px; height: 115px;
    background: var(--white); display: flex; align-items: center; justify-content: center; gap: 10px;
  }
  .brand-box__dot { width: 18px; height: 18px; border-radius: 50%; background: var(--navy); }
  .brand-box__name {
    font-family: "PT Sans", sans-serif; font-size: 28px; font-weight: 700; color: #1d3b6e;
  }

  .order-button {
    position: absolute; right: 16px; width: 214px; height: 72px;
    border: 2px solid var(--white); border-radius: 8px;
    background: linear-gradient(to bottom, var(--button-top) 0%, #8ccbea 48%, var(--button-bottom) 52%, #6bb6df 100%);
    display: flex; align-items: center; justify-content: center;
    font-family: "PT Sans", sans-serif; font-weight: 700; font-size: 28px; letter-spacing: 1px;
    color: var(--white); text-transform: uppercase;
  }
  .banner--order .order-button { top: 33px; }
  .banner--sky .order-button { top: 30px; }

  .caption {
    position: absolute; left: 0; width: 1200px; top: 752px; text-align: center;
    font-family: "PT Sans", sans-serif; font-size: 27px; line-height: 36px; color: var(--caption);
  }
</style>
</head>
<body>
<main class="canvas">

  <section class="banner banner--save">
    <div class="photo photo--pets" role="img" aria-label="Photo of a small dog and a tabby cat lying together"></div>
    <p class="headline headline--save">Save on genuine brand<br>tick and flea products</p>
    <div class="photo photo--pugs" role="img" aria-label="Photo of three pugs sitting in a row"></div>
  </section>

  <section class="banner banner--brand">
    <div class="banner__frame"></div>
    <div class="photo photo--pets" role="img" aria-label="Photo of a small dog and a tabby cat lying together"></div>
    <p class="headline headline--protect">Protect your pets from Ticks and Fleas</p>
    <div class="brand-box">
      <span class="brand-box__dot"></span>
      <span class="brand-box__name">Global Paw Store</span>
    </div>
  </section>

  <section class="banner banner--order">
    <div class="banner__frame"></div>
    <div class="photo photo--pets" role="img" aria-label="Photo of a small dog and a tabby cat lying together"></div>
    <p class="headline headline--protect">Protect your pets from Ticks and Fleas</p>
    <a class="order-button">Order Now</a>
  </section>

  <section class="banner banner--sky">
    <div class="banner__frame"></div>
    <div class="photo photo--terrier" role="img" aria-label="Photo of a small terrier puppy lying down"></div>
    <p class="headline headline--navy">Protect your pets from Ticks and Fleas</p>
    <p class="site-url">globalpawstore.com</p>
    <a class="order-button">Order Now</a>
  </section>

  <p class="caption">view external link:<br>http://www.swfviewhub.com/k4Pm2Qx</p>

</main>
</body>
</html>
```